Design concept for BrightKestrel.com Support Page

We are about to launch a new support page for our www.brightkestrel.com service for photographers and visual artists. The service provides media management, cloud storage, promotional and secure distribution to our members.

The support page will include FAQs and video tutorials.

In particular we're looking for a header for this page that suggests the user is in the support area of our service - so perhaps an illustration that suggests support could look nice (perhaps repair man or doctor iconography). Something to give this area of our site a different look and something that looks both cool and friendly.

Currently the page looks distinctly sparse and undesigned (see attached screenshot) - something that could be remedied, we feel, by some subtle design enhancements that we can implement using CSS.

```html
<!DOCTYPE html>
<html lang="en">
<head>
<meta charset="utf-8">
<title>BrightKestrel Support</title>
<link rel="stylesheet" href="https://fonts.googleapis.com/css2?family=Fira+Sans:wght@400;500;600&family=Open+Sans:wght@300;400&display=swap">
<style>
:root{
  --ink:#3a3a3a;
  --text:#555b61;
  --muted:#6c6c6c;
  --accent:#1e9fc0;
  --accent-bright:#1eaed0;
  --slate:#636b74;
  --band:#ededed;
  --white:#ffffff;
  --footer:#000000;
  --footer-link:#a6a6a6;
  --search-field:#bdbdbd;
  --search-btn:#3d3d3d;
}
*{box-sizing:border-box;margin:0;padding:0}
html,body{width:823px;height:1200px;overflow:hidden}
body{position:relative;background:var(--white);font-family:"Open Sans",sans-serif;color:var(--text)}

.site-header{position:absolute;left:0;top:0;width:823px;height:65px;background:var(--white)}
.brand{position:absolute;left:16px;top:16px;display:flex;align-items:center;gap:9px;font-family:"Fira Sans",sans-serif;font-weight:600;font-size:25px;color:#58595b;line-height:1}
.brand-mark{width:26px;height:26px;border:3px solid #58595b;border-radius:4px}
.user-menu{position:absolute;left:702px;top:23px;width:109px;height:24px;border:1px solid #d4d4d4;border-radius:2px;display:flex;align-items:center;padding-left:5px;font-size:10px;color:#333;font-family:"Open Sans",sans-serif}
.user-avatar{width:18px;height:16px;background:linear-gradient(135deg,#8a7a6c,#4c4038);margin-right:6px}
.user-caret{position:absolute;right:8px;top:9px;width:0;height:0;border-left:3px solid transparent;border-right:3px solid transparent;border-top:4px solid #888}

.hero{position:absolute;left:0;top:65px;width:823px;height:230px;background:
  radial-gradient(ellipse at 70% 45%,#5fd0f2 0%,#2fb3e3 35%,#1a8ebf 75%,#126b94 100%);overflow:hidden}
.hero-illustration{position:absolute;left:29px;top:44px;width:206px;height:143px;border-radius:40px;background:radial-gradient(circle at 55% 50%,#f6a623 0%,#e7891a 45%,rgba(120,170,200,.6) 75%,rgba(120,170,200,0) 100%)}
.hero-kicker{position:absolute;left:257px;top:62px;font-family:"Open Sans",sans-serif;font-weight:400;font-size:28px;color:var(--white);letter-spacing:.3px}
.hero-title{position:absolute;left:255px;top:98px;font-family:"Open Sans",sans-serif;font-weight:300;font-size:54px;color:var(--white);white-space:nowrap}

.tutorials{position:absolute;left:0;top:295px;width:823px;height:357px;background:var(--band)}
.section-title{font-family:"Fira Sans",sans-serif;font-weight:600;font-size:25px;color:var(--ink);text-align:center}
.section-lead{font-size:12px;line-height:14.5px;color:var(--text);text-align:center;width:600px;margin:0 auto}
.tutorials .section-title{position:absolute;top:30px;width:100%}
.tutorials .section-lead{position:absolute;top:68px;left:111px}
.carousel-arrow{position:absolute;top:180px}
.carousel-arrow.prev{left:14px}
.carousel-arrow.next{left:784px}
.video-card{position:absolute;top:129px;width:175px}
.video-thumb{position:relative;width:175px;height:126px}
.video-thumb svg{position:absolute;left:58px;top:34px}
.video-title{margin-top:9px;font-family:"Fira Sans",sans-serif;font-weight:600;font-size:13px;color:var(--accent)}
.video-desc{margin-top:5px;font-size:9.5px;line-height:12px;color:var(--muted)}

.faq{position:absolute;left:0;top:652px;width:823px;height:426px;background:var(--white)}
.faq .section-title{position:absolute;top:38px;width:100%}
.faq .section-lead{position:absolute;top:76px;left:111px}
.faq-search{position:absolute;left:272px;top:120px;display:flex}
.faq-search-field{width:212px;height:27px;background:var(--search-field);border:0}
.faq-search-btn{width:73px;height:27px;margin-left:1px;background:var(--search-btn);color:var(--white);font-size:12px;display:flex;align-items:center;justify-content:center}
.faq-list{position:absolute;left:73px;top:185px;width:681px;list-style:none}
.faq-item{height:33px;margin-bottom:0.6px;background:var(--slate);border-radius:3px;display:flex;align-items:center;color:var(--white);font-size:12.5px}
.faq-item.is-active{background:var(--accent-bright)}
.faq-toggle{width:17px;height:17px;border-radius:50%;background:var(--white);margin:0 16px 0 20px;display:flex;align-items:center;justify-content:center;color:var(--accent);font-weight:700;font-size:13px;line-height:1}

.site-footer{position:absolute;left:0;top:1078px;width:823px;height:122px;background:var(--footer);text-align:center;font-family:"Fira Sans",sans-serif}
.footer-nav{position:absolute;top:27px;width:100%;font-size:11px;color:var(--footer-link)}
.footer-nav span.sep{margin:0 7px}
.copyright{position:absolute;top:62px;width:100%;font-size:10.5px;color:var(--white);font-weight:500}
.powered{position:absolute;top:78px;width:100%;font-size:10.5px;color:#6f6f6f}
</style>
</head>
<body>

<header class="site-header">
  <div class="brand"><span class="brand-mark"></span>BrightKestrel</div>
  <div class="user-menu">
    <span class="user-avatar" role="img" aria-label="Member profile photo"></span>
    Mara Lindqvist
    <span class="user-caret"></span>
  </div>
</header>

<section class="hero">
  <div class="hero-illustration" role="img" aria-label="Illustration of a friendly repair character in a hard hat holding a wrench and toolbox"></div>
  <p class="hero-kicker">BrightKestrel Support</p>
  <h1 class="hero-title">We’re happy to help …</h1>
</section>

<section class="tutorials">
  <h2 class="section-title">Video Tutorials</h2>
  <p class="section-lead">Lorem ipsum dolor sit amet, consectetur adipisicing elit, sed do eiusmod tempor incididunt ut labore et dolore magna aliqua. Ut enim ad minim veniam, quis nostrud exercitation ullamco laboris.</p>

  <svg class="carousel-arrow prev" width="24" height="34" viewBox="0 0 24 34"><path d="M20 3 L6 17 L20 31" fill="none" stroke="#666" stroke-width="6"/></svg>
  <svg class="carousel-arrow next" width="24" height="34" viewBox="0 0 24 34"><path d="M4 3 L18 17 L4 31" fill="none" stroke="#666" stroke-width="6"/></svg>

  <article class="video-card" style="left:55px">
    <div class="video-thumb" role="img" aria-label="Photo of a camera hanging from a strap" style="background:linear-gradient(135deg,#c9b79a,#6d5a44 45%,#cfc6a8)">
      <svg width="60" height="60" viewBox="0 0 60 60"><circle cx="30" cy="30" r="27" fill="rgba(255,255,255,.15)" stroke="rgba(255,255,255,.8)" stroke-width="3"/><path d="M23 17 L43 30 L23 43Z" fill="rgba(255,255,255,.8)"/></svg>
    </div>
    <h3 class="video-title">Lorem ipsum dolor</h3>
    <p class="video-desc">Lorem ipsum dolor sit amet, consectetur adipisicing elit, sed.</p>
  </article>

  <article class="video-card" style="left:234px">
    <div class="video-thumb" role="img" aria-label="Photo of a hand throwing colourful powder" style="background:linear-gradient(135deg,#6a4a2a,#3f7a46 45%,#2b8fa8 75%,#1b2a1c)">
      <svg width="60" height="60" viewBox="0 0 60 60"><circle cx="30" cy="30" r="27" fill="rgba(255,255,255,.15)" stroke="rgba(255,255,255,.8)" stroke-width="3"/><path d="M23 17 L43 30 L23 43Z" fill="rgba(255,255,255,.8)"/></svg>
    </div>
    <h3 class="video-title">Do eiusmod tempor</h3>
    <p class="video-desc">Do eiusmod tempor incididunt ut labore et dolore magna aliqua.</p>
  </article>

  <article class="video-card" style="left:413px">
    <div class="video-thumb" role="img" aria-label="Photo of a dark stone resting on water droplets" style="background:linear-gradient(180deg,#0e3f5a,#1f7fa0 55%,#a7d3e0)">
      <svg width="60" height="60" viewBox="0 0 60 60"><circle cx="30" cy="30" r="27" fill="rgba(255,255,255,.15)" stroke="rgba(255,255,255,.8)" stroke-width="3"/><path d="M23 17 L43 30 L23 43Z" fill="rgba(255,255,255,.8)"/></svg>
    </div>
    <h3 class="video-title">Ut enim ad minim</h3>
    <p class="video-desc">Ut enim ad minim veniam, quis nostrd exercittion ullam laboris.</p>
  </article>

  <article class="video-card" style="left:592px">
    <div class="video-thumb" role="img" aria-label="Photo of a photographer silhouetted above the clouds at sunset" style="background:linear-gradient(90deg,#e9c98a,#b8a785 50%,#1d2430 80%)">
      <svg width="60" height="60" viewBox="0 0 60 60"><circle cx="30" cy="30" r="27" fill="rgba(255,255,255,.15)" stroke="rgba(255,255,255,.8)" stroke-width="3"/><path d="M23 17 L43 30 L23 43Z" fill="rgba(255,255,255,.8)"/></svg>
    </div>
    <h3 class="video-title">Lorem ipsum dolor</h3>
    <p class="video-desc">Lorem ipsum dolor sit amet, consectetur adipisicing elit, sed.</p>
  </article>
</section>

<section class="faq">
  <h2 class="section-title">Frequently Asked Questions</h2>
  <p class="section-lead">Lorem ipsum dolor sit amet, consectetur adipisicing elit, sed do eiusmod tempor incididunt ut labore et dolore magna aliqua. Ut enim ad minim veniam, quis nostrud exercitation ullamco laboris.</p>
  <div class="faq-search">
    <div class="faq-search-field"></div>
    <div class="faq-search-btn">search</div>
  </div>
  <ul class="faq-list">
    <li class="faq-item is-active"><span class="faq-toggle">+</span>Uploading Files Using the Drag and Drop Uploader</li>
    <li class="faq-item"><span class="faq-toggle">+</span>Publishing Files</li>
    <li class="faq-item"><span class="faq-toggle">+</span>Creating Galleries</li>
    <li class="faq-item"><span class="faq-toggle">+</span>Creating Portfolios</li>
    <li class="faq-item"><span class="faq-toggle">+</span>Re-ordering Files within Galleries of Portfolios</li>
    <li class="faq-item"><span class="faq-toggle">+</span>Managing Folder and Files</li>
  </ul>
</section>

<footer class="site-footer">
  <nav class="footer-nav">
    Home<span class="sep">·</span>Contact Us<span class="sep">·</span>Affiliate Program<span class="sep">·</span>Privacy Policy<span class="sep">·</span>Site Terms and Conditions<span class="sep">·</span>About Us
  </nav>
  <p class="copyright">© Copyright 2014 Northgate Images Pte Ltd. All rights reserved.</p>
  <p class="powered">Powered by BrightKestrel</p>
</footer>

</body>
</html>
```